RB Halden Electric Yard Sign

Looking to have a yard sign designed that we can place at projects we are working on. Most likely will be 18" H x 24" W but flexible that we can increase the size if necessary. It should include our logo, our phone # 609-555-0147, website rbhaldenelectric.example and slogan, built on integrity, driven by excellence. Colors should match our brand.

```html
<!DOCTYPE html>
<html lang="en">
<head>
<meta charset="utf-8">
<title>RB Halden Electric – Yard Sign</title>
<link rel="stylesheet" href="https://fonts.googleapis.com/css2?family=Lato:wght@900&family=Saira+Condensed:wght@600;700;800&display=swap">
<style>
  :root {
    --brand-red: #ee1c2b;
    --brand-navy: #12335a;
    --sign-white: #ffffff;
    --band-grey-light: #f2f2f2;
    --band-grey-mid: #d3d3d3;
    --ink: #111111;
    --backdrop: #e8eae6;
  }
  * { margin: 0; padding: 0; box-sizing: border-box; }
  html, body {
    width: 1200px;
    height: 1029px;
    overflow: hidden;
    background: var(--backdrop);
  }
  .yard-sign {
    position: absolute;
    left: 50px;
    top: 102px;
    width: 1100px;
    height: 825px;
    background: var(--sign-white);
    overflow: hidden;
    box-shadow: 0 6px 20px rgba(0,0,0,0.12);
  }
  .brand-name {
    position: absolute;
    left: 0;
    right: 0;
    top: 160px;
    display: flex;
    justify-content: center;
    align-items: center;
    gap: 22px;
    white-space: nowrap;
  }
  .brand-name__mark {
    width: 54px;
    height: 54px;
    background: var(--brand-navy);
    flex: none;
  }
  .brand-name__text {
    font-family: "Saira Condensed", sans-serif;
    font-weight: 800;
    font-size: 96px;
    line-height: 1;
    color: var(--brand-red);
    letter-spacing: 2px;
  }
  .trade-line {
    position: absolute;
    left: 0;
    right: 0;
    top: 270px;
    text-align: center;
    font-family: "Lato", sans-serif;
    font-weight: 900;
    font-size: 46px;
    line-height: 1;
    letter-spacing: 12px;
    color: var(--brand-navy);
    padding-left: 12px;
    white-space: nowrap;
  }
  .trade-rule {
    position: absolute;
    left: 139px;
    top: 318px;
    width: 824px;
    height: 16px;
  }
  .phone-band {
    position: absolute;
    left: 0;
    top: 366px;
    width: 100%;
    height: 192px;
    background: var(--brand-red);
    display: flex;
    align-items: center;
    justify-content: center;
  }
  .phone-band__number {
    font-family: "Saira Condensed", sans-serif;
    font-weight: 800;
    font-size: 158px;
    line-height: 1;
    color: var(--sign-white);
    letter-spacing: 10px;
    white-space: nowrap;
  }
  .web-tab {
    position: absolute;
    left: 0;
    top: 558px;
    width: 1100px;
    height: 110px;
  }
  .web-tab__address {
    position: absolute;
    left: 0;
    right: 0;
    top: 576px;
    text-align: center;
    font-family: "Saira Condensed", sans-serif;
    font-weight: 700;
    font-size: 50px;
    line-height: 52px;
    color: var(--sign-white);
    letter-spacing: 2px;
    white-space: nowrap;
  }
  .slogan-band {
    position: absolute;
    left: 0;
    top: 683px;
    width: 100%;
    height: 142px;
    padding: 0 40px;
    background: linear-gradient(90deg, var(--band-grey-light) 0%, var(--band-grey-mid) 18%, var(--band-grey-light) 45%, var(--band-grey-mid) 75%, var(--band-grey-light) 100%);
    display: flex;
    align-items: center;
    justify-content: center;
  }
  .slogan-band__text {
    font-family: "Saira Condensed", sans-serif;
    font-weight: 700;
    font-size: 62px;
    line-height: 1;
    color: var(--ink);
    white-space: nowrap;
    text-align: center;
  }
</style>
</head>
<body>
  <main class="yard-sign">
    <div class="brand-name">
      <span class="brand-name__mark"></span>
      <span class="brand-name__text">RB Halden Electric</span>
    </div>
    <p class="trade-line">Electrical Contractor</p>
    <svg class="trade-rule" viewBox="0 0 824 16" aria-hidden="true">
      <polygon points="0,2 824,2 810,8 14,8" fill="var(--brand-red)"/>
      <polygon points="14,8 810,8 800,15 24,15" fill="var(--brand-navy)"/>
    </svg>

    <section class="phone-band">
      <span class="phone-band__number">609-555-0147</span>
    </section>

    <svg class="web-tab" viewBox="0 0 1100 110" aria-hidden="true">
      <polyline points="129,0 190,105 910,105 971,0" fill="none" stroke="var(--brand-navy)" stroke-width="3"/>
      <polygon points="146,0 955,0 898,95 202,95" fill="var(--brand-navy)"/>
    </svg>
    <p class="web-tab__address">www.rbhaldenelectric.example</p>

    <section class="slogan-band">
      <span class="slogan-band__text">Built on Integrity, Driven by Excellence</span>
    </section>
  </main>
</body>
</html>
```